Web site for small printshop

I am looking for a website for small printshop in Iceland, mainly serving university students and artist.

We print posters, flyers, business cards and more.

In addition to our current website, I would like to include design tool, (fx. www.quarvelpad.example, www.trindomap.example or something similar) jobs upload, shopping chart.
Updates

Great work, I am really amazed of the quality of work i am seeing here.

Really way beyond my expectation

GOOD JOB - all of you ! 

Hi all.

The designs submitted have been great, way better than expected.
I really did not expect this level of quality.

Some have been asking me for feedback on their designs, and I will try 
to send some feedback here, without spoiling your creativity.

Likes:
- when the colors of my logo is used in menus, buttons etc.
- simple, not to crowded look.

Dislikes.
- Dark and heavy design
- Lot of text and buttons (crowded look)

Extra info.
- top line (before menus) will contain: Tel - email - language
- menu line will have 5 categories: Home - service - submission of works - FAQ - about us
- 3 large buttons:  Job submit - Job design - ask for offer

LOVE YOUR WORK - great designs so far :)

Target Market(s)

University Students, Artists. Age group 20-30

Industry/Entity Type

University

Requirements
Must have
• The website must be easy to use, clean looking.

```html
<!DOCTYPE html>
<html lang="en">
<head>
<meta charset="utf-8">
<title>Prenthúsið – Print shop</title>
<link href="https://fonts.googleapis.com/css2?family=Oswald:wght@500&family=PT+Sans:wght@400;700&display=swap" rel="stylesheet">
<style>
  :root {
    --red: #ee3a2c;
    --green: #1f7a35;
    --green-dark: #136b2c;
    --ink: #333333;
    --ink-soft: #555555;
    --grey-line: #dddddd;
    --footer: #141414;
    --white: #ffffff;
  }
  * { box-sizing: border-box; margin: 0; padding: 0; }
  html, body { width: 906px; height: 1200px; overflow: hidden; background: var(--white); }
  body { position: relative; font-family: "PT Sans", sans-serif; color: var(--ink); }
  .abs { position: absolute; }

  .top-band { left: 0; top: 0; width: 906px; height: 5px; background: var(--red); }

  .brand { left: 65px; top: 41px; display: flex; align-items: center; gap: 9px; }
  .brand-mark { width: 32px; height: 40px; background: var(--red); }
  .brand-name { font-size: 27px; font-weight: 700; color: var(--ink); letter-spacing: 0.5px; }

  .phone { right: 65px; top: 22px; display: flex; align-items: center; gap: 9px; font-size: 19px; color: #666; }

  .nav { left: 0; top: 63px; width: 906px; height: 22px; }
  .nav a { position: absolute; font-size: 13px; color: var(--ink); text-decoration: none; text-transform: uppercase; }
  .nav a.is-active { border-bottom: 2px solid var(--red); padding-bottom: 2px; }
  .nav a.is-active::after { content: ""; position: absolute; left: 50%; bottom: -6px; margin-left: -4px;
    border-left: 4px solid transparent; border-right: 4px solid transparent; border-top: 4px solid var(--red); }

  .hero { left: 65px; top: 97px; width: 776px; height: 287px; border: 1px solid var(--grey-line); overflow: hidden; }
  .hero-photo { position: absolute; inset: 0;
    background: linear-gradient(90deg, #8a8a8a 0%, #b4b4b4 25%, #dadada 50%, #f4f4f4 68%, #ffffff 80%); }
  .hero-copy { position: absolute; left: 530px; top: 86px; width: 240px; }
  .hero-title { font-family: "Oswald", sans-serif; font-weight: 500; font-size: 24px; color: var(--red); line-height: 1.1; }
  .hero-sub { font-size: 17px; color: var(--ink); margin-top: 4px; letter-spacing: 0.2px; }
  .hero-text { font-size: 12.2px; line-height: 19px; color: var(--ink); margin-top: 7px; }
  .hero-dots { position: absolute; right: 15px; bottom: 10px; display: flex; gap: 4px; }
  .hero-dots span { width: 6px; height: 6px; border-radius: 50%; background: #333; }
  .hero-dots span.is-open { background: transparent; border: 1px solid #333; }

  .step { top: 416px; width: 230px; text-align: center; }
  .step-label { font-size: 15.5px; font-weight: 700; color: var(--green); letter-spacing: 0.5px; }
  .step-badge { width: 110px; height: 110px; margin: 16px auto 0; border-radius: 50%;
    background: radial-gradient(circle at 50% 40%, #ffffff 0%, #f2f2f2 55%, #dcdcdc 100%);
    box-shadow: 0 4px 8px rgba(0,0,0,0.15); display: flex; align-items: center; justify-content: center; }
  .step-title { font-size: 16px; font-weight: 400; color: var(--ink); margin-top: 8px; }
  .step-text { font-size: 10.5px; line-height: 16.5px; color: var(--ink); margin-top: 4px; letter-spacing: 0.2px; }

  .section-title { font-size: 16px; font-weight: 400; color: var(--green-dark); }
  .body-text { font-size: 10px; line-height: 17.5px; color: var(--ink-soft); }

  .welcome-photo { left: 67px; top: 694px; width: 166px; height: 160px;
    background: linear-gradient(135deg, #e9a24a 0%, #d94b6a 35%, #5ab0d8 65%, #f0d03a 100%); border-radius: 2px; }
  .welcome-lead { left: 249px; top: 690px; width: 325px; font-size: 12.3px; line-height: 20px; color: var(--ink); }
  .welcome-text { left: 249px; top: 736px; width: 330px; }

  .where-photo { left: 617px; top: 694px; width: 223px; height: 105px;
    background: linear-gradient(180deg, #5b5b5b 0%, #9a9a9a 40%, #d99aa0 75%, #c95a6a 100%); }
  .where-text { left: 617px; top: 810px; width: 225px; }

  .service { top: 893px; width: 176px; }
  .service-frame { margin-top: 9px; width: 174px; height: 116px; border: 1px solid var(--grey-line); padding: 3px; }
  .service-frame div { width: 100%; height: 100%; }
  .service-text { margin-top: 11px; font-size: 10px; line-height: 16.5px; color: var(--ink-soft); }

  .footer { left: 0; top: 1122px; width: 906px; height: 78px; background: var(--footer); color: var(--white); }
  .footer-links { position: absolute; left: 65px; top: 18px; font-size: 10.5px; }
  .footer-copy { position: absolute; left: 65px; top: 44px; font-size: 10.5px; }
  .social { position: absolute; left: 703px; top: 25px; display: flex; gap: 10px; }
  .social span { width: 27px; height: 27px; display: block; }
</style>
</head>
<body>
  <div class="abs top-band"></div>

  <div class="abs brand">
    <span class="brand-mark"></span>
    <span class="brand-name">PRENTHÚSIÐ</span>
  </div>

  <div class="abs phone">
    <svg width="19" height="19" viewBox="0 0 20 20" aria-hidden="true">
      <circle cx="10" cy="10" r="10" fill="#9a9a9a"/>
      <path d="M7 5.5c-.6.3-1.2 1-1.1 2 .3 2.6 3.6 6 6.3 6.5 1 .2 1.7-.4 2-1l-1.9-1.6-1.1.9c-1.2-.5-2.3-1.7-2.9-2.9l.9-1.1L7 5.5z" fill="#fff"/>
    </svg>
    <span>555-017-2846</span>
  </div>

  <nav class="abs nav">
    <a class="is-active" href="#" style="left:464px">Home</a>
    <a href="#" style="left:532px">Demo</a>
    <a href="#" style="left:599px">Store</a>
    <a href="#" style="left:669px">FAQ</a>
    <a href="#" style="left:725px">Blog</a>
    <a href="#" style="left:789px">Support</a>
  </nav>

  <section class="abs hero">
    <div class="hero-photo" role="img" aria-label="Close-up photograph of an eye with a multicoloured iris"></div>
    <div class="hero-copy">
      <h1 class="hero-title">PELLENTESQUE CURSUS</h1>
      <p class="hero-sub">DIGNISSIM PHARETRA ERO</p>
      <p class="hero-text">Jerta baditaut onsequser untur magni dolori es eoquie voluptate msequi nesciunt. Volupt atem accusantium dolorem.</p>
    </div>
    <div class="hero-dots"><span class="is-open"></span><span></span><span></span><span></span></div>
  </section>

  <div class="abs step" style="left:81px">
    <div class="step-label">STEP 1</div>
    <div class="step-badge">
      <svg width="64" height="54" viewBox="0 0 64 54" aria-hidden="true">
        <rect x="3" y="3" width="58" height="44" fill="none" stroke="#136b2c" stroke-width="4"/>
        <rect x="11" y="12" width="42" height="4" fill="#136b2c"/>
        <rect x="11" y="21" width="42" height="4" fill="#136b2c"/>
        <rect x="11" y="30" width="30" height="4" fill="#136b2c"/>
        <path d="M45 28l10 14-5 1 3 6-3 1-3-6-4 3z" fill="#136b2c"/>
      </svg>
    </div>
    <div class="step-title">Create a Design</div>
    <p class="step-text">Lorem ipsum dolor sit amet adipis<br>ing elit.Morbi ut elipsum tristique acc<br>Pellentesque habitant morbi.</p>
  </div>

  <div class="abs step" style="left:328px">
    <div class="step-label">STEP 2</div>
    <div class="step-badge">
      <svg width="60" height="60" viewBox="0 0 60 60" aria-hidden="true">
        <circle cx="30" cy="30" r="26" fill="none" stroke="#136b2c" stroke-width="5"/>
        <circle cx="30" cy="30" r="17" fill="#136b2c"/>
        <path d="M30 18l11 12h-6v14h-10V30h-6z" fill="#fff"/>
      </svg>
    </div>
    <div class="step-title">Upload your Design</div>
    <p class="step-text">Lorem ipsum dolor sit amet adipis<br>ing elit.Morbi ut elipsum tristique acc<br>Pellentesque habitant morbi.</p>
  </div>

  <div class="abs step" style="left:587px">
    <div class="step-label">STEP 3</div>
    <div class="step-badge">
      <svg width="62" height="56" viewBox="0 0 62 56" aria-hidden="true">
        <rect x="14" y="2" width="34" height="10" rx="2" fill="#136b2c"/>
        <rect x="2" y="14" width="58" height="24" rx="5" fill="#136b2c"/>
        <circle cx="10" cy="21" r="2" fill="#fff"/><circle cx="16" cy="21" r="2" fill="#fff"/>
        <path d="M16 32h30v20H16z" fill="#fff" stroke="#136b2c" stroke-width="4"/>
        <rect x="22" y="39" width="18" height="3" fill="#136b2c"/>
        <rect x="22" y="45" width="12" height="3" fill="#136b2c"/>
      </svg>
    </div>
    <div class="step-title">Getting it Printed</div>
    <p class="step-text">Lorem ipsum dolor sit amet adipis<br>ing elit.Morbi ut elipsum tristique acc<br>Pellentesque habitant morbi.</p>
  </div>

  <h2 class="abs section-title" style="left:66px; top:657px">Welcome to our website</h2>
  <div class="abs welcome-photo" role="img" aria-label="Colour swatch fan and a loupe on a printed colour chart"></div>
  <p class="abs welcome-lead">Ut wisi enim ad minim veniam, quis nostrud exerci tation ulli amcorper suscipit lobortis nisl ut aliquip exea.</p>
  <p class="abs body-text welcome-text">Incididunt ut labore et dolore magna aliqua. Ut enim ad minim veniam, quis nostrud exercitation ullamcolaboris nisi ut aliquip ex ea commodo consequat. Duis tefd&nbsp; aute iruredolor inreprehenderit in&nbsp; voluptate velit esse cillum.Dolore magna aliqua. Ut enim ad minim veniam, Quisnostru dexercitation ullamco laboris nisi ut aliquip. Ut enim ad mini m veniam, quis nostrud exercitation ullamco laboris. Claritas est etiam p rocessus dynamicus, qui sequitur mutationem.</p>

  <h2 class="abs section-title" style="left:619px; top:657px">Where we are?</h2>
  <div class="abs where-photo" role="img" aria-label="Printing press hall with printed sheets on the conveyor"></div>
  <p class="abs body-text where-text">Duis autem vel eum iriure dolor in hendrerit in vu l.Ut wisi enim ad minim veniam, quis nostrud. Uti wisi enim ad minim veniam, quis nostrud.</p>

  <div class="abs service" style="left:65px">
    <h2 class="section-title">Photocopying</h2>
    <div class="service-frame"><div role="img" aria-label="Office worker at a photocopier" style="background:linear-gradient(135deg,#c9dbe6,#eef3f6 60%,#b8c9d4)"></div></div>
    <p class="service-text">Lorem ipsum dolor sit amet, consectet uer adipiscing elit. Mauris vel tortor vit ae nibh condimentum auctor.</p>
  </div>
  <div class="abs service" style="left:265px">
    <h2 class="section-title">Printing</h2>
    <div class="service-frame"><div role="img" aria-label="Desktop printer feeding a sheet" style="background:linear-gradient(160deg,#8a4a3a,#5a5a5a 40%,#e6e6e6 85%)"></div></div>
    <p class="service-text">Lorem ipsum dolor sit amet, consectet uer adipiscing elit. Mauris vel tortor vit ae nibh condimentum auctor.</p>
  </div>
  <div class="abs service" style="left:467px">
    <h2 class="section-title">Book publishing</h2>
    <div class="service-frame"><div role="img" aria-label="Colour test sheets running through a press" style="background:linear-gradient(120deg,#d6409a,#e8d22e 35%,#3a9ad6 65%,#4fb34a)"></div></div>
    <p class="service-text">Lorem ipsum dolor sit amet, consectet uer adipiscing elit. Mauris vel tortor vit ae nibh condimentum auctor.</p>
  </div>
  <div class="abs service" style="left:666px">
    <h2 class="section-title">University Printing</h2>
    <div class="service-frame"><div role="img" aria-label="Stacks of printed papers coming off a press line" style="background:linear-gradient(160deg,#4a4a4a,#9a9a9a 50%,#c8383a)"></div></div>
    <p class="service-text">Lorem ipsum dolor sit amet, consectet uer adipiscing elit. Mauris vel tortor vit ae nibh condimentum auctor.</p>
  </div>

  <footer class="abs footer">
    <div class="footer-links">Home | Demo | Store | FAQ | Blog | Support</div>
    <div class="footer-copy">Copyrights 2013. All Rights Reserved.</div>
    <div class="social" aria-label="Social links">
      <span style="background:#3b5ba3"></span>
      <span style="background:#1e9ad6"></span>
      <span style="background:#f07d14"></span>
      <span style="background:#d4252a"></span>
    </div>
  </footer>
</body>
</html>
```